Business card por a urban DJ, up scale audience target

Need a sober design, modern, conservative colors but i can consider some options, y play rnb, hip hop, EDM and top40.

Business card for contact and personal info, double sided, use logo attrached please; im 42 so i need a card acording to my age an target audience.

Target Market(s)

Adult people, up scale audience

Industry/Entity Type

Music Download

Contact Information for Business Card

Cel (318) 4207265518 www.lumadrift.com

Requirements
Must have
• open mind
Nice to have
• open mind
Should not have
• DJ

```html
<!DOCTYPE html>
<html lang="en">
<head>
<meta charset="utf-8">
<title>Luma Business Card</title>
<link href="https://fonts.googleapis.com/css2?family=Archivo:wght@400;800&display=swap" rel="stylesheet">
<style>
  :root {
    --stage: #d8d6d2;
    --ink: #141414;
    --card-dark: #1b1b1b;
    --card-dark-hi: #3d3d3d;
    --paper: #ffffff;
    --silver-hi: #f4f4f4;
    --silver-lo: #b9b9b9;
    --text-light: #e9e9e9;
    --text-muted: #c9c9c9;
  }
  * { margin: 0; padding: 0; box-sizing: border-box; }
  html, body {
    width: 1200px;
    height: 950px;
    overflow: hidden;
    background: var(--stage);
    font-family: "Archivo", Arial, sans-serif;
  }
  .sheet {
    width: 1200px;
    height: 950px;
    display: flex;
    flex-direction: column;
    align-items: center;
    justify-content: center;
    gap: 50px;
  }
  .card {
    width: 700px;
    height: 400px;
    position: relative;
    overflow: hidden;
    box-shadow: 0 10px 28px rgba(0,0,0,0.25);
  }
  .wordmark {
    font-family: "Archivo", Arial, sans-serif;
    font-weight: 800;
    letter-spacing: 2px;
    color: var(--ink);
    line-height: 1;
  }

  /* Front side */
  .card--front {
    background: linear-gradient(100deg, var(--card-dark) 0%, var(--card-dark) 52%, var(--card-dark-hi) 68%, var(--card-dark) 100%);
  }
  .front__panel {
    position: absolute;
    left: 30px;
    top: 30px;
    width: 340px;
    height: 340px;
    background: var(--paper);
    display: flex;
    align-items: center;
    justify-content: center;
  }
  .front__panel .wordmark { font-size: 96px; }
  .front__details {
    position: absolute;
    left: 400px;
    top: 150px;
    color: var(--text-light);
  }
  .details__name {
    font-size: 21px;
    font-weight: 400;
    letter-spacing: 1.5px;
    text-transform: uppercase;
  }
  .details__title {
    font-size: 15px;
    letter-spacing: 1px;
    text-transform: uppercase;
    color: var(--text-muted);
    margin-top: 4px;
  }
  .details__contact {
    list-style: none;
    margin-top: 26px;
    font-size: 17px;
    line-height: 1.55;
    color: var(--text-light);
  }

  /* Back side */
  .card--back {
    background: linear-gradient(120deg, var(--silver-lo) 0%, var(--silver-hi) 45%, var(--silver-lo) 100%);
    display: flex;
    flex-direction: column;
    align-items: center;
    justify-content: center;
  }
  .card--back .wordmark { font-size: 110px; }
  .back__url {
    margin-top: 14px;
    font-size: 16px;
    letter-spacing: 2.5px;
    text-transform: uppercase;
    color: var(--ink);
  }
</style>
</head>
<body>
  <main class="sheet">
    <section class="card card--front" aria-label="Card front">
      <div class="front__panel">
        <span class="wordmark">LUMA</span>
      </div>
      <div class="front__details">
        <p class="details__name">Mark Ellis</p>
        <p class="details__title">President</p>
        <ul class="details__contact">
          <li>(318) 4207265518</li>
          <li>www.lumadrift.com</li>
        </ul>
      </div>
    </section>

    <section class="card card--back" aria-label="Card back">
      <span class="wordmark">LUMA</span>
      <p class="back__url">lumadrift.com</p>
    </section>
  </main>
</body>
</html>
```